KVOR Individual and Corporate Development Business Card Design

KVOR needs a business card design that is aligned with it's values and targetted markets. Coherent Lattice of Adaptive Reasoning Method's self diagnosis model and tools, which can be used for personal improvement and team/business performance enhancement, is based on the learnings of over 20 years of medical practitioning. KVOR supercharges personal effectiveness and awareness to also increase team and business performance.

The targetted markets are high performance individuals and teams who aspire seek to enhance their capabilities and achieve their absolute best potential.

Look and feel for the business card design we are looking for is high technology, premium, fresh, new and medical.

Target Market(s)

Industry/Entity Type

Business Consultant

Contact Information for Business Card

Logo, Full Name, Title, Phone number, Email, company name, Address,

Font styles to use
Sans Serif

Requirements
Must have
• Tag line: Sharpening Potential for Driven Teams and Leaders
• Please use same colours as the logo.

```html
<!DOCTYPE html>
<html lang="en">
<head>
<meta charset="utf-8">
<title>KVOR Business Card</title>
<link rel="stylesheet" href="https://fonts.googleapis.com/css2?family=Raleway:wght@600;700;800&family=Source+Sans+3:wght@400;600&display=swap">
<style>
  :root {
    --stage: #000000;
    --paper: #ffffff;
    --teal: #07a8c3;
    --ink: #1b1b1b;
    --on-teal: #ffffff;
  }
  * { margin: 0; padding: 0; box-sizing: border-box; }
  html, body { width: 1200px; height: 900px; overflow: hidden; background: var(--stage); }
  .canvas { position: relative; width: 1200px; height: 900px; }
  .card {
    position: absolute; top: 170px; width: 347px; height: 561px;
    text-align: center;
    font-family: "Source Sans 3", sans-serif;
  }
  .card--front { left: 259px; background: var(--paper); color: var(--ink); }
  .card--back { left: 631px; background: var(--teal); color: var(--on-teal); }

  .brand { position: absolute; left: 0; right: 0; }
  .card--front .brand { top: 88px; color: var(--teal); }
  .card--back .brand { top: 98px; color: var(--on-teal); }
  .brand__name {
    font-family: "Raleway", sans-serif; font-weight: 800;
    font-size: 54px; line-height: 1; letter-spacing: 4px;
  }
  .brand__full {
    margin-top: 16px;
    font-family: "Raleway", sans-serif; font-weight: 700;
    font-size: 14px; line-height: 17px; letter-spacing: 0.4px;
    text-transform: uppercase;
  }

  .contact { position: absolute; left: 0; right: 0; top: 318px; font-size: 15px; line-height: 21px; text-transform: uppercase; }
  .contact__name { color: var(--teal); font-size: 25px; line-height: 30px; letter-spacing: 0.5px; }
  .contact__title { margin-top: 2px; }
  .contact__rule { width: 102px; height: 2px; background: var(--teal); margin: 12px auto 10px; }
  .contact__label { color: var(--teal); font-weight: 600; }
  .contact__web { color: var(--teal); font-weight: 600; }

  .tagline {
    position: absolute; left: 0; right: 0; top: 330px;
    font-family: "Raleway", sans-serif; font-weight: 700;
    font-size: 31px; line-height: 38px; letter-spacing: 3px;
    text-transform: uppercase;
  }
</style>
</head>
<body>
<main class="canvas">
  <section class="card card--front">
    <div class="brand">
      <div class="brand__name">KVOR</div>
      <div class="brand__full">Individual &amp; Corporate<br>Development</div>
    </div>
    <div class="contact">
      <div class="contact__name">Daniel Reyes</div>
      <div class="contact__title">Managing Director</div>
      <div class="contact__rule"></div>
      <div><span class="contact__label">P:</span> 823-456-7890</div>
      <div><span class="contact__label">E:</span> info@youremail.com</div>
      <div class="contact__web">www.websitename.com</div>
      <div class="contact__rule"></div>
      <div>1234, Address Goes Here</div>
      <div>Country Name, 123456</div>
    </div>
  </section>

  <section class="card card--back">
    <div class="brand">
      <div class="brand__name">KVOR</div>
      <div class="brand__full">Individual &amp; Corporate<br>Development</div>
    </div>
    <p class="tagline">Sharpening<br>Potential<br>for Driven<br>Teams and<br>Leaders</p>
  </section>
</main>
</body>
</html>
```